Business Card for Coastal Tundrabridge Advisory

We need a business card for Coastal Tundrabridge Advisory. The company website address is provided below. The company logo is attached. We provide specialized permafrost services to the mining, transportation, and oil & gas industries. The card should be prepared for:
Matthias Korhonen, PhD.
Coastal Tundrabridge Advisory
PO Box 418259
Quillwater, Alaska 99642
Direct: +1-907-555-0143
Email: mkorhonen@tundrabridgeadvisory.example
Website: www.coastaltundrabridgeadvisory.example

```html
<!DOCTYPE html>
<html lang="en">
<head>
<meta charset="utf-8">
<title>Coastal Tundrabridge Advisory — Business Card</title>
<link href="https://fonts.googleapis.com/css2?family=Roboto:wght@300;400;700&display=swap" rel="stylesheet">
<style>
  :root {
    --backdrop: #232323;
    --card: #ffffff;
    --ink: #141a24;
    --band: #0f1620;
    --muted: #2b2f36;
  }
  * { box-sizing: border-box; margin: 0; padding: 0; }
  html, body {
    width: 1200px; height: 711px; overflow: hidden;
    background: var(--backdrop);
    font-family: "Roboto", Arial, sans-serif;
    color: var(--ink);
  }
  .stage { position: relative; width: 1200px; height: 711px; }
  .card {
    position: absolute; top: 201px;
    width: 540px; height: 309px;
    background: var(--card);
    overflow: hidden;
  }
  .card--front { left: 40px; }
  .card--back { left: 620px; }

  .band { position: absolute; width: 14px; background: var(--band); }
  .band--left { left: 0; top: 36%; height: 44%; }
  .band--right { right: 0; top: 10%; height: 40%; }

  .brand {
    position: absolute;
    font-weight: 700; text-transform: uppercase;
    color: var(--ink); line-height: 1.15;
    display: flex; align-items: center; gap: 10px;
  }
  .brand__mark { width: 12px; height: 12px; background: var(--ink); flex: none; }
  .card--front .brand {
    left: 0; right: 0; top: 0; bottom: 0;
    justify-content: center;
    font-size: 30px; letter-spacing: 3px;
  }
  .card--back .brand {
    left: 30px; top: 128px; width: 196px;
    font-size: 17px; letter-spacing: 1.5px;
  }

  .divider { position: absolute; left: 238px; top: 70px; width: 40px; height: 170px; }

  .person { position: absolute; left: 284px; top: 56px; width: 236px; }
  .person__name { font-size: 25px; line-height: 1.1; white-space: nowrap; }
  .person__first { font-weight: 700; }
  .person__last { font-weight: 300; }
  .person__title { font-size: 14px; font-weight: 700; margin-top: 2px; }

  .contacts { list-style: none; margin-top: 22px; }
  .contacts li {
    display: flex; align-items: center; gap: 6px;
    font-size: 10.5px; line-height: 1; margin-bottom: 7px;
    color: var(--muted); white-space: nowrap;
  }
  .contacts svg { width: 11px; height: 11px; flex: none; fill: var(--ink); }

  .address {
    position: absolute; left: 284px; bottom: 34px;
    font-size: 12px; color: var(--muted); white-space: nowrap;
  }
</style>
</head>
<body>
<main class="stage">
  <section class="card card--front" aria-label="Card front">
    <span class="band band--left"></span>
    <span class="band band--right"></span>
    <div class="brand"><span class="brand__mark"></span><span>Coastal Tundrabridge<br>Advisory</span></div>
  </section>

  <section class="card card--back" aria-label="Card back">
    <span class="band band--left"></span>
    <span class="band band--right"></span>
    <div class="brand"><span class="brand__mark"></span><span>Coastal<br>Tundrabridge<br>Advisory</span></div>

    <svg class="divider" viewBox="0 0 40 170" aria-hidden="true">
      <line x1="2" y1="0" x2="38" y2="170" stroke="#141a24" stroke-width="1"/>
    </svg>

    <div class="person">
      <p class="person__name"><span class="person__first">Matthias</span> <span class="person__last">Korhonen</span></p>
      <p class="person__title">PhD</p>
      <ul class="contacts">
        <li>
          <svg viewBox="0 0 24 24"><path d="M6.6 10.8a15.1 15.1 0 0 0 6.6 6.6l2.2-2.2a1 1 0 0 1 1-.25 11.4 11.4 0 0 0 3.6.57 1 1 0 0 1 1 1V20a1 1 0 0 1-1 1A17 17 0 0 1 3 4a1 1 0 0 1 1-1h3.5a1 1 0 0 1 1 1c0 1.25.2 2.45.57 3.57a1 1 0 0 1-.25 1z"/></svg>
          +1-907-555-0143
        </li>
        <li>
          <svg viewBox="0 0 24 24"><path d="M2 5h20v14H2z M4 7v.4l8 5 8-5V7l-8 5z" fill-rule="evenodd"/></svg>
          mkorhonen@tundrabridgeadvisory.example
        </li>
        <li>
          <svg viewBox="0 0 24 24"><circle cx="12" cy="12" r="10"/></svg>
          www.coastaltundrabridgeadvisory.example
        </li>
      </ul>
    </div>

    <p class="address">PO Box 418259 Quillwater, Alaska 99642</p>
  </section>
</main>
</body>
</html>
```